Web Design for guards MMJ transport and security services

Harbor Crest Protective solutions a tallow unified company, is looking for a designer to create a website that displays our service portfolio. We need marketing pictures and content to be created in a original and competitive fashion, intriguing to our customers. We will need forms on the website to be created for calendar booking (somehow integrate into exchange if possible) and general inquiry forms. There will need to be pages dedicated to our staff, MMJ trasnport & Courier services, our vehicles, alarm systems, video systems, video monitoring, private investigations, and surveillance aduit and compliance investigations, payment gateway integration, and general company information. I Have attached our main company logo. Also have a emphasis on being state licensed by the Colorado RPB. Have a link to our parent site, tallowcctv.example

Target Market(s)

Colorado Marijuana industry, MMJ transport services, guard services, armed gaurd services.

Contact Information for Business Card

Would like a sleek simple design highlighting what we offer. must match the website and have a overall professional straight to the point appearance.

Number of Pages Required

1 page

Colors
33b8a4
00a990
9bcb3c
acd036
cadf82
85cae6
33a6d7
0792cd

Requirements
Must have
• Easy to use, lots of images, professional.
Nice to have
• Creativity

```html
<!DOCTYPE html>
<html lang="en">
<head>
<meta charset="utf-8">
<title>Harbor Crest Protective Solutions</title>
<link rel="stylesheet" href="https://fonts.googleapis.com/css2?family=Arimo:ital,wght@0,400;0,700;1,400&family=Open+Sans:ital,wght@0,400;0,600;0,700;1,400&display=swap">
<style>
:root{
  --green:#8cc63e;
  --blue:#33a6d7;
  --blue-bar:#3aa3d3;
  --teal:#33b8a4;
  --ink:#2b2b2b;
  --text:#6b6b6b;
  --pale:#eef1f4;
  --footer:#1f1f1f;
  --footer-line:#333;
  --footer-text:#d4d4d4;
  --badge:#c9cfd6;
  --white:#fff;
  --crest:#b8202c;
}
*{box-sizing:border-box;margin:0;padding:0}
html,body{width:1200px;height:2416px;overflow:hidden}
body{position:relative;background:var(--white);font-family:"Open Sans",Arial,sans-serif;color:var(--text)}
.abs{position:absolute}
h2,h3,h4{font-family:"Arimo",Arial,sans-serif;color:var(--ink)}

/* header */
.topline{left:0;top:0;width:1200px;height:4px;background:linear-gradient(90deg,var(--teal),var(--blue),var(--green))}
.header{left:0;top:4px;width:1200px;height:86px;background:var(--white)}
.brand-disc{left:88px;top:-40px;width:168px;height:186px;border-radius:50%;background:var(--white);z-index:3;display:flex;align-items:center;justify-content:center;gap:6px;padding-top:70px}
.brand-dot{width:14px;height:14px;border-radius:50%;background:var(--crest)}
.brand-name{font-family:"Arimo",Arial,sans-serif;font-weight:700;font-size:17px;color:var(--crest);line-height:1.1}
.contact-row{right:86px;top:16px;display:flex;align-items:center;font-size:14px;color:var(--ink)}
.social{display:flex;gap:7px;margin-right:28px}
.social span{width:26px;height:26px;border-radius:50%}
.social .s1{background:#3b5a9a}.social .s2{background:#2aa3ef}.social .s3{background:#d9313a}
.ring{width:28px;height:28px;border-radius:50%;border:2px solid var(--green);display:flex;align-items:center;justify-content:center;margin-right:8px}
.contact-item{display:flex;align-items:center;margin-left:16px}
.nav{right:86px;top:64px;display:flex;gap:24px;font-family:"Arimo",Arial,sans-serif;font-weight:700;font-size:13px;color:var(--ink);align-items:center}
.nav .active{color:var(--green)}

/* hero */
.hero{left:0;top:90px;width:1200px;height:369px;background:linear-gradient(180deg,#8fb2cf 0%,#b9c8d6 35%,#7d8791 62%,#555b60 100%)}
.hero-title{left:0;top:194px;width:1200px;text-align:center;color:var(--white);font-family:"Arimo",Arial,sans-serif;font-weight:700;text-shadow:0 2px 6px rgba(0,0,0,.55)}
.hero-title .small{font-size:37px;display:block;line-height:1.1}
.hero-title .big{font-size:57px;display:block;line-height:1.1}
.btn-video{left:504px;top:315px;width:192px;height:50px;background:var(--green);color:var(--white);font-family:"Arimo",Arial,sans-serif;font-weight:700;font-size:16px;display:flex;align-items:center;justify-content:center;gap:8px}
.hero-arrow{top:298px}

/* feature bar */
.feature-bar{left:0;top:459px;width:1200px;height:77px;background:var(--blue-bar)}
.feature{position:absolute;top:0;height:77px;display:flex;align-items:center;gap:18px;color:var(--white);font-size:15px;line-height:1.35}
.feature-sep{position:absolute;top:8px;width:1px;height:61px;background:rgba(255,255,255,.3)}

/* welcome */
.welcome-title{left:98px;top:578px;font-size:25px;font-weight:700}
.welcome-text{left:98px;top:626px;width:672px;font-size:12px;line-height:2}
.readmore{font-family:"Arimo",Arial,sans-serif;font-weight:700;font-size:12.5px;color:var(--green)}
.badge{left:846px;top:568px;width:190px;height:190px;border-radius:50%;background:var(--badge)}

/* what we do */
.services{left:0;top:803px;width:1200px;height:437px;background:var(--pale)}
.services-title{left:0;top:842px;width:1200px;text-align:center;font-size:24px;font-weight:700}
.card{top:947px;width:305px;height:236px;background:var(--white);text-align:center;padding-top:70px}
.card h3{font-size:16px;font-weight:700;margin-bottom:16px}
.card p{font-size:12px;line-height:1.85;padding:0 22px;margin-bottom:18px}
.card.c-green{border-bottom:4px solid var(--green)}
.card.c-blue{border-bottom:4px solid var(--blue)}
.card.c-teal{border-bottom:4px solid var(--teal)}
.card-icon{top:899px;width:100px;height:100px;border-radius:50%;background:var(--white);display:flex;align-items:center;justify-content:center}
.card-icon span{width:86px;height:86px;border-radius:50%;display:flex;align-items:center;justify-content:center}
.i-green{border:2px solid var(--green)}.i-green span{background:var(--green)}
.i-blue{border:2px solid var(--blue)}.i-blue span{background:var(--blue)}
.i-teal{border:2px solid var(--teal)}.i-teal span{background:var(--teal)}

/* strengths band */
.strengths{left:0;top:1240px;width:1200px;height:135px;background:linear-gradient(90deg,#3a3330 0%,#5b4a45 35%,#4a3b3b 55%,#6a5a55 75%,#3b3532 100%)}
.strength{top:1268px;width:200px;text-align:center;color:var(--white);font-family:"Arimo",Arial,sans-serif;font-weight:700;font-size:15.5px;text-shadow:0 1px 3px rgba(0,0,0,.6)}
.strength svg{display:block;margin:0 auto 12px}

/* who we are / news */
.col-title{top:1412px;font-size:22px;font-weight:700}
.who-photo{left:98px;top:1470px;width:374px;height:209px;background:linear-gradient(180deg,#7b8691,#9aa3a7 55%,#5d6467);border:4px solid var(--white);box-shadow:0 0 0 1px #ddd}
.who-text{left:98px;top:1693px;width:380px;font-size:12px;line-height:1.8}
.checks{left:98px;top:1756px;list-style:none;font-size:12px}
.checks li{display:flex;align-items:center;gap:10px;height:31px}
.news-item{left:525px;width:575px;height:137px;border-bottom:1px solid #e2e2e2}
.news-thumb{position:absolute;left:0;top:0;width:111px;height:97px;border:3px solid var(--white);box-shadow:0 0 0 1px #ddd}
.news-body{position:absolute;left:137px;top:0;width:430px}
.news-body h4{font-size:13.5px;font-weight:700;margin-bottom:9px}
.news-date{display:flex;align-items:center;gap:8px;color:var(--blue);font-size:12px;margin-bottom:8px}
.news-body p{font-size:12px;line-height:1.8}

/* testimonial */
.testimonial{left:0;top:1942px;width:1200px;height:166px;background:var(--green)}
.quote-disc{left:150px;top:1961px;width:118px;height:118px;border-radius:50%;background:#e3e3e3;display:flex;align-items:center;padding-left:24px;font-family:Georgia,serif;font-size:70px;color:var(--white);line-height:1}
.person{left:221px;top:1965px;width:112px;height:112px;border-radius:50%;background:linear-gradient(180deg,#d9d9d9,#8a8f96);border:3px solid var(--white)}
.quote-text{left:365px;top:1970px;width:680px;color:var(--white);font-style:italic;font-size:13px;line-height:2.05}
.quote-name{left:365px;top:2062px;color:var(--white);font-family:"Arimo",Arial,sans-serif;font-weight:700;font-size:15px}

/* footer */
.footer{left:0;top:2108px;width:1200px;height:308px;background:var(--footer);color:var(--footer-text)}
.foot-brand{left:80px;top:2206px;font-family:"Arimo",Arial,sans-serif;font-size:30px;font-weight:700;color:var(--blue);letter-spacing:1px}
.foot-col{color:var(--footer-text)}
.foot-col h4{color:var(--white);font-size:16px;font-weight:700;margin-bottom:22px}
.foot-col ul{list-style:none;font-size:12px;line-height:2.6}
.foot-sep{top:2140px;width:1px;height:190px;background:var(--footer-line)}
.news-form p{font-size:12px;line-height:1.8;width:270px;margin-bottom:10px}
.news-input{width:263px;height:32px;background:var(--white);color:#999;font-size:12px;padding:8px 14px}
.news-btn{margin-top:13px;width:99px;height:36px;border:2px solid var(--white);color:var(--white);font-family:"Arimo",Arial,sans-serif;font-weight:700;font-size:12px;display:flex;align-items:center;justify-content:center}
.foot-col .contact-list{line-height:1.6}
.contact-list li{display:flex;gap:14px;align-items:flex-start;margin-bottom:17px}
.foot-rule{left:0;top:2354px;width:1200px;height:1px;background:var(--footer-line)}
.copyright{left:100px;top:2374px;font-size:12px;color:var(--footer-text)}
.foot-social{left:980px;top:2368px;display:flex;gap:6px}
.foot-social span{width:28px;height:28px;border-radius:50%;border:1.5px solid var(--footer-text)}
</style>
</head>
<body>

<!-- header -->
<div class="abs topline"></div>
<header class="abs header"></header>
<div class="abs brand-disc"><span class="brand-dot"></span><span class="brand-name">Harbor<br>Crest</span></div>

<div class="abs contact-row">
  <div class="social"><span class="s1"></span><span class="s2"></span><span class="s3"></span></div>
  <div class="contact-item"><span class="ring"><svg width="14" height="14" viewBox="0 0 24 24"><path fill="#8cc63e" d="M6.6 10.8a15 15 0 0 0 6.6 6.6l2.2-2.2a1 1 0 0 1 1-.25 11.4 11.4 0 0 0 3.6.57 1 1 0 0 1 1 1V20a1 1 0 0 1-1 1A17 17 0 0 1 3 4a1 1 0 0 1 1-1h3.5a1 1 0 0 1 1 1c0 1.25.2 2.45.57 3.57a1 1 0 0 1-.25 1z"/></svg></span>+1 555 014 2290</div>
  <div class="contact-item"><span class="ring"><svg width="14" height="12" viewBox="0 0 14 11"><rect width="14" height="11" fill="#8cc63e"/><path d="M0 0l7 6 7-6" fill="none" stroke="#fff" stroke-width="1.3"/></svg></span>info@harborcrestprotective.example</div>
</div>

<nav class="abs nav">
  <span class="active">HOME</span><span>ABOUT US</span><span>OUR STAFF</span><span>MMJ TRASNPORT &amp; COURIER SERVICES</span><span>OUR VEHICLES</span><span>MORE ▾</span>
  <svg width="13" height="13" viewBox="0 0 24 24"><circle cx="10" cy="10" r="7" fill="none" stroke="#2b2b2b" stroke-width="3"/><path d="M15 15l7 7" stroke="#2b2b2b" stroke-width="3"/></svg>
</nav>

<!-- hero -->
<section class="abs hero" role="img" aria-label="Inspection truck parked at a harbor checkpoint with cranes in the background"></section>
<div class="abs hero-title"><span class="small">HARBOR CREST</span><span class="big">PROTECTIVE SOLUTIONS</span></div>
<div class="abs btn-video">WATCH VIDEO <svg width="15" height="15" viewBox="0 0 24 24"><circle cx="12" cy="12" r="11" fill="#fff"/><path d="M10 7l6 5-6 5z" fill="#8cc63e"/></svg></div>
<svg class="abs hero-arrow" style="left:44px" width="16" height="30" viewBox="0 0 16 30"><path d="M14 2L3 15l11 13" fill="none" stroke="#fff" stroke-width="2.5"/></svg>
<svg class="abs hero-arrow" style="left:1140px" width="16" height="30" viewBox="0 0 16 30"><path d="M2 2l11 13L2 28" fill="none" stroke="#fff" stroke-width="2.5"/></svg>

<!-- feature bar -->
<section class="abs feature-bar">
  <div class="feature" style="left:134px"><svg width="38" height="38" viewBox="0 0 38 38"><circle cx="19" cy="19" r="18" fill="#fff"/><text x="19" y="27" text-anchor="middle" font-family="Arimo,Arial,sans-serif" font-weight="700" font-size="24" fill="#3aa3d3">?</text></svg><span>Why Harbor<br>Protective solutions</span></div>
  <span class="feature-sep" style="left:395px"></span>
  <div class="feature" style="left:433px"><svg width="48" height="40" viewBox="0 0 48 40"><circle cx="16" cy="18" r="10" fill="none" stroke="#fff" stroke-width="6" stroke-dasharray="5 3"/><circle cx="16" cy="18" r="4" fill="#fff"/><circle cx="36" cy="30" r="7" fill="none" stroke="#fff" stroke-width="4" stroke-dasharray="3 2"/><circle cx="36" cy="10" r="5" fill="none" stroke="#fff" stroke-width="3" stroke-dasharray="3 2"/></svg><span>Find out<br>How it works</span></div>
  <span class="feature-sep" style="left:645px"></span>
  <div class="feature" style="left:697px"><svg width="38" height="38" viewBox="0 0 38 38"><rect x="1" y="1" width="36" height="36" rx="6" fill="#fff"/><path d="M12 10l4 0 2 6-3 2a12 12 0 0 0 5 5l2-3 6 2v4a2 2 0 0 1-2 2A18 18 0 0 1 10 12a2 2 0 0 1 2-2z" fill="#3aa3d3"/></svg><span>Emergency<br>Response</span></div>
  <span class="feature-sep" style="left:886px"></span>
  <div class="feature" style="left:950px"><svg width="34" height="42" viewBox="0 0 34 42"><path d="M1 1h22l10 10v30H1z" fill="#fff"/><path d="M7 18h20M7 24h20M7 30h20" stroke="#3aa3d3" stroke-width="2.5"/></svg><span>Get<br>a Quote</span></div>
</section>

<!-- welcome -->
<h2 class="abs welcome-title">WELCOME TO HARBOR CREST PROTECTIVE SOLUTIONS</h2>
<p class="abs welcome-text">Nemo enim ipsam voluptatem quia voluptas sit aspernatur aut odit aut fugit, sed quia consequuntur magni dolores eos qui ratione voluptatem sequi nesciunt dolorem ipsum quia dolor sit amet, consectetur, adipisci velit, sed quia non num quam eius modi tempora incidunt ut labore et But I must explain to you how all this mistaken idea of denouncing plea sure and praising pain was born and I will give you a complete account..</p>
<span class="abs readmore" style="left:98px;top:744px">READ MORE &gt;&gt;</span>
<div class="abs badge" role="img" aria-label="State licensing badge"></div>

<!-- what we do -->
<section class="abs services"></section>
<h2 class="abs services-title">WHAT WE DO</h2>

<div class="abs card c-green" style="left:98px"><h3>Investigation &amp; Surveillance</h3><p>Sed ut perspiciatis unde omnis iste natus error sit voluptatem accusantium doloremque laudantiuque ipsquasetsi adi</p><span class="readmore">READ MORE &gt;&gt;</span></div>
<div class="abs card c-blue" style="left:448px"><h3>Access Control</h3><p>Sed ut perspiciatis unde omnis iste natus error sit voluptatem accusantium doloremque laudantiuque ipsquasetsi adi</p><span class="readmore">READ MORE &gt;&gt;</span></div>
<div class="abs card c-teal" style="left:795px"><h3>Audit &amp; Security</h3><p>Sed ut perspiciatis unde omnis iste natus error sit voluptatem accusantium doloremque laudantiuque ipsquasetsi adi</p><span class="readmore">READ MORE &gt;&gt;</span></div>

<div class="abs card-icon i-green" style="left:200px"><span><svg width="40" height="34" viewBox="0 0 40 34"><path d="M3 8h9l3-5h10l3 5h9v24H3z" fill="#fff"/><circle cx="20" cy="19" r="8" fill="#8cc63e"/><circle cx="20" cy="19" r="5" fill="#fff"/></svg></span></div>
<div class="abs card-icon i-blue" style="left:550px"><span><svg width="40" height="40" viewBox="0 0 40 40"><rect x="6" y="3" width="22" height="32" rx="3" fill="#fff"/><rect x="10" y="7" width="14" height="7" fill="#33a6d7"/><g fill="#33a6d7"><rect x="10" y="17" width="3" height="3"/><rect x="15.5" y="17" width="3" height="3"/><rect x="21" y="17" width="3" height="3"/><rect x="10" y="23" width="3" height="3"/><rect x="15.5" y="23" width="3" height="3"/></g><rect x="20" y="22" width="16" height="11" rx="1" fill="#fff" stroke="#33a6d7" stroke-width="1.5" transform="rotate(-25 28 27)"/></svg></span></div>
<div class="abs card-icon i-teal" style="left:897px"><span><svg width="30" height="36" viewBox="0 0 30 36"><path d="M7 16v-6a8 8 0 0 1 16 0v6" fill="none" stroke="#fff" stroke-width="4"/><rect x="2" y="15" width="26" height="20" rx="2" fill="#fff"/></svg></span></div>

<!-- strengths band -->
<section class="abs strengths" role="img" aria-label="Night highway with light trails"></section>
<div class="abs strength" style="left:88px"><svg width="44" height="44" viewBox="0 0 44 44"><circle cx="22" cy="22" r="19" fill="none" stroke="#fff" stroke-width="4"/><path d="M22 11v12h8" fill="none" stroke="#fff" stroke-width="4"/></svg>24 Hour Control Centre</div>
<div class="abs strength" style="left:294px"><svg width="48" height="44" viewBox="0 0 48 46"><path d="M24 2l6.5 14 15 1.5-11.3 10 3.3 15L24 35l-13.5 7.5 3.3-15L2.5 17.5l15-1.5z" fill="#fff"/></svg>Experienced</div>
<div class="abs strength" style="left:502px"><svg width="36" height="44" viewBox="0 0 36 44"><path d="M2 2h22l10 10v30H2z" fill="none" stroke="#fff" stroke-width="3"/><path d="M8 18h20M8 25h20M8 32h20" stroke="#fff" stroke-width="3"/></svg>Powerful Reporting</div>
<div class="abs strength" style="left:710px"><svg width="36" height="44" viewBox="0 0 36 44"><path d="M8 20v-8a10 10 0 0 1 20 0v8" fill="none" stroke="#fff" stroke-width="5"/><rect x="3" y="19" width="30" height="23" rx="2" fill="#fff"/></svg>High Quality Security</div>
<div class="abs strength" style="left:916px"><svg width="32" height="44" viewBox="0 0 32 44"><path d="M16 2a13 13 0 0 0-8 23c2 2 2 4 2 7h12c0-3 0-5 2-7A13 13 0 0 0 16 2z" fill="none" stroke="#fff" stroke-width="3"/><path d="M10 36h12M11 41h10" stroke="#fff" stroke-width="3"/></svg>Intelligence Solutions</div>

<!-- who we are -->
<h2 class="abs col-title" style="left:98px">WHO WE ARE</h2>
<div class="abs who-photo" role="img" aria-label="Police officers in high-visibility vests at a roadside vehicle checkpoint"></div>
<p class="abs who-text">Nemo enim ipsam voluptatem quia voluptas sit aspernatur aut odit aut fugit, sed quia consequuntur magni,..</p>
<ul class="abs checks">
  <li><svg width="13" height="13" viewBox="0 0 14 14"><circle cx="7" cy="7" r="7" fill="#33a6d7"/><path d="M4 7.2l2 2 4-4" fill="none" stroke="#fff" stroke-width="1.6"/></svg>22% higher profitability</li>
  <li><svg width="13" height="13" viewBox="0 0 14 14"><circle cx="7" cy="7" r="7" fill="#33a6d7"/><path d="M4 7.2l2 2 4-4" fill="none" stroke="#fff" stroke-width="1.6"/></svg>21% higher productivity</li>
  <li><svg width="13" height="13" viewBox="0 0 14 14"><circle cx="7" cy="7" r="7" fill="#33a6d7"/><path d="M4 7.2l2 2 4-4" fill="none" stroke="#fff" stroke-width="1.6"/></svg>37% lower absenteeism</li>
  <li><svg width="13" height="13" viewBox="0 0 14 14"><circle cx="7" cy="7" r="7" fill="#33a6d7"/><path d="M4 7.2l2 2 4-4" fill="none" stroke="#fff" stroke-width="1.6"/></svg>Up to 65% less turnover of staff.</li>
</ul>
<span class="abs readmore" style="left:98px;top:1892px">READ MORE &gt;&gt;</span>

<!-- news -->
<h2 class="abs col-title" style="left:522px">OUR NEWS</h2>
<article class="abs news-item" style="top:1470px">
  <div class="news-thumb" role="img" aria-label="Roadside checkpoint with a stop sign" style="background:linear-gradient(180deg,#9aa7b2,#6b747b)"></div>
  <div class="news-body"><h4>AT VERO EOS ET ACCUSAMUS ET IUSTO ODIO DIG</h4><div class="news-date"><svg width="12" height="12" viewBox="0 0 12 12"><rect x="0.5" y="1.5" width="11" height="10" fill="none" stroke="#33a6d7"/><path d="M0.5 4.5h11" stroke="#33a6d7"/></svg>05/03/2016</div><p>Nemo enim ipsam voluptatem quia voluptas sit aspernatur aut odit aut fugit, sed quia consequuntur..</p></div>
</article>
<article class="abs news-item" style="top:1607px">
  <div class="news-thumb" role="img" aria-label="Operator speaking on a headset" style="background:linear-gradient(180deg,#8aa0b8,#4f5f72)"></div>
  <div class="news-body"><h4>AT VERO EOS ET ACCUSAMUS ET IUSTO ODIO DIG</h4><div class="news-date"><svg width="12" height="12" viewBox="0 0 12 12"><rect x="0.5" y="1.5" width="11" height="10" fill="none" stroke="#33a6d7"/><path d="M0.5 4.5h11" stroke="#33a6d7"/></svg>05/03/2016</div><p>Nemo enim ipsam voluptatem quia voluptas sit aspernatur aut odit aut fugit, sed quia consequuntur..</p></div>
</article>
<article class="abs news-item" style="top:1744px">
  <div class="news-thumb" role="img" aria-label="Officers in yellow vests beside a patrol car" style="background:linear-gradient(180deg,#6f7a6a,#3e443c)"></div>
  <div class="news-body"><h4>AT VERO EOS ET ACCUSAMUS ET IUSTO ODIO DIG</h4><div class="news-date"><svg width="12" height="12" viewBox="0 0 12 12"><rect x="0.5" y="1.5" width="11" height="10" fill="none" stroke="#33a6d7"/><path d="M0.5 4.5h11" stroke="#33a6d7"/></svg>05/03/2016</div><p>Nemo enim ipsam voluptatem quia voluptas sit aspernatur aut odit aut fugit, sed quia consequuntur..</p></div>
</article>
<span class="abs readmore" style="left:527px;top:1888px">VIEW MORE &gt;&gt;</span>

<!-- testimonial -->
<section class="abs testimonial"></section>
<div class="abs quote-disc">“</div>
<div class="abs person" role="img" aria-label="Portrait of a client in a suit"></div>
<p class="abs quote-text">It is a long established fact that a reader will be distracted by the readable content of a page when looking at its layout. The point of using Lorem Ipsum is that it has a more-or-less normal distribution of letters, as opposed to using 'Content here, content here', making it look like readable English.</p>
<span class="abs quote-name">- Daniel Hartley</span>
<svg class="abs" style="left:100px;top:2010px" width="14" height="24" viewBox="0 0 14 24"><path d="M12 2L3 12l9 10" fill="none" stroke="#fff" stroke-width="3"/></svg>
<svg class="abs" style="left:1086px;top:2010px" width="14" height="24" viewBox="0 0 14 24"><path d="M2 2l9 10-9 10" fill="none" stroke="#fff" stroke-width="3"/></svg>

<!-- footer -->
<footer class="abs footer"></footer>
<div class="abs foot-brand">TALLOW UNIFIED</div>
<span class="abs foot-sep" style="left:356px"></span>
<div class="abs foot-col" style="left:378px;top:2138px">
  <h4>Quick Links</h4>
  <ul><li>Account Manager</li><li>Project Manager</li><li>Installation Technician</li><li>Service Technician</li></ul>
</div>
<span class="abs foot-sep" style="left:532px"></span>
<div class="abs foot-col news-form" style="left:557px;top:2138px">
  <h4>Newsletter</h4>
  <p>Register your email address to get information ablout us</p>
  <div class="news-input">Email Address</div>
  <div class="news-btn">SUBSCRIBE</div>
</div>
<span class="abs foot-sep" style="left:845px"></span>
<div class="abs foot-col" style="left:868px;top:2138px">
  <h4>Contact Us</h4>
  <ul class="contact-list">
    <li><svg width="12" height="14" viewBox="0 0 12 16"><path d="M6 0a6 6 0 0 0-6 6c0 4.5 6 10 6 10s6-5.5 6-10a6 6 0 0 0-6-6z" fill="#fff"/><circle cx="6" cy="6" r="2.2" fill="#1f1f1f"/></svg><span>58 Juniper Ridge Road<br>Alder Falls, CO 80917</span></li>
    <li><svg width="12" height="12" viewBox="0 0 24 24"><path fill="#fff" d="M6.6 10.8a15 15 0 0 0 6.6 6.6l2.2-2.2a1 1 0 0 1 1-.25 11.4 11.4 0 0 0 3.6.57 1 1 0 0 1 1 1V20a1 1 0 0 1-1 1A17 17 0 0 1 3 4a1 1 0 0 1 1-1h3.5a1 1 0 0 1 1 1c0 1.25.2 2.45.57 3.57a1 1 0 0 1-.25 1z"/></svg><span>+1 555 014 2290</span></li>
    <li><svg width="14" height="12" viewBox="0 0 14 12"><rect x="0" y="3" width="14" height="9" fill="#fff"/><rect x="3" y="0" width="8" height="4" fill="#fff"/><rect x="3" y="6" width="8" height="3" fill="#1f1f1f"/></svg><span>+1 555 014 2291</span></li>
    <li><svg width="14" height="11" viewBox="0 0 14 11"><rect width="14" height="11" fill="#fff"/><path d="M0 0l7 6 7-6" fill="none" stroke="#1f1f1f" stroke-width="1.3"/></svg><span>info@harborcrest.example</span></li>
  </ul>
</div>
<div class="abs foot-rule"></div>
<span class="abs copyright">Copyrights © 2016, Harbor Crest Protective solutions. All rights reserved.</span>
<div class="abs foot-social"><span></span><span></span><span></span><span></span></div>

</body>
</html>
```